Accounting firm needing business card / letterhead designed
Marcus L. Trenholm, CPA
marcus@veltrowledger.com
www.veltrowledger.com
842 E Alder Ave Brenmoor, IA 43827
608-562-0974

```html
<!DOCTYPE html>
<html lang="en">
<head>
<meta charset="utf-8">
<title>Veltro Ledger – Business Card</title>
<link rel="stylesheet" href="https://fonts.googleapis.com/css2?family=Montserrat:wght@400;500;600&display=swap">
<style>
  :root {
    --stage: #2a2a2c;
    --card: #1c1c1d;
    --card-edge: #262627;
    --green: #7dc242;
    --navy: #2f2b86;
    --white: #f2f2f2;
  }
  * { box-sizing: border-box; margin: 0; padding: 0; }
  html, body { width: 1200px; height: 900px; overflow: hidden; }
  body {
    background: var(--stage);
    font-family: "Montserrat", Arial, sans-serif;
    color: var(--white);
    display: flex;
    flex-direction: column;
    align-items: center;
    justify-content: center;
    gap: 40px;
  }
  .card {
    width: 700px;
    height: 400px;
    background: linear-gradient(135deg, var(--card) 0%, var(--card-edge) 100%);
    box-shadow: 0 12px 30px rgba(0,0,0,.45);
    position: relative;
  }
  /* Front */
  .card--front .wordmark {
    position: absolute;
    top: 150px; left: 0; right: 0;
    text-align: center;
    font-size: 46px;
    font-weight: 500;
    letter-spacing: 6px;
    color: var(--white);
  }
  .card--front .web {
    position: absolute;
    bottom: 40px; left: 0; right: 0;
    text-align: center;
    font-size: 15px;
    letter-spacing: 1.5px;
  }
  .accent { color: var(--green); }
  /* Back */
  .card--back .wordmark {
    position: absolute;
    left: 40px; top: 148px;
    width: 310px;
    font-size: 38px;
    font-weight: 500;
    letter-spacing: 3px;
    line-height: 1.05;
    color: var(--navy);
  }
  .divider {
    position: absolute;
    left: 375px; top: 118px;
    width: 2px; height: 130px;
    background: var(--green);
  }
  .contact {
    position: absolute;
    left: 400px; top: 118px;
  }
  .contact .name {
    font-size: 21px;
    font-weight: 600;
    color: var(--green);
    text-transform: uppercase;
    line-height: 1;
  }
  .contact .title {
    font-size: 15px;
    font-weight: 500;
    margin: 4px 0 12px;
  }
  .contact ul { list-style: none; }
  .contact li {
    display: flex; align-items: center; gap: 12px;
    font-size: 15px;
    letter-spacing: .5px;
    line-height: 26px;
  }
  .contact svg { width: 16px; height: 16px; flex: none; }
  .address {
    position: absolute;
    bottom: 36px; left: 0; right: 0;
    text-align: center;
    font-size: 17px;
    letter-spacing: .5px;
  }
</style>
</head>
<body>
  <section class="card card--front">
    <div class="wordmark">VELTRO LEDGER</div>
    <div class="web">www.<span class="accent">veltrowledger</span>.com</div>
  </section>

  <section class="card card--back">
    <div class="wordmark">VELTRO<br>LEDGER</div>
    <div class="divider"></div>
    <div class="contact">
      <div class="name">Marcus L. Trenholm</div>
      <div class="title">CPA</div>
      <ul>
        <li>
          <svg viewBox="0 0 16 16" fill="none" stroke="#7dc242" stroke-width="1.4"><rect x="4" y="1" width="8" height="14" rx="1.5"/><line x1="7" y1="12.5" x2="9" y2="12.5"/></svg>
          608-562-0974
        </li>
        <li>
          <svg viewBox="0 0 16 16"><rect x="1" y="3" width="14" height="10" fill="#7dc242"/><path d="M1 3l7 6 7-6" fill="none" stroke="#1c1c1d" stroke-width="1.3"/></svg>
          marcus@veltrowledger.com
        </li>
        <li>
          <svg viewBox="0 0 16 16" fill="none" stroke="#7dc242" stroke-width="1.3"><circle cx="8" cy="8" r="6.5"/><ellipse cx="8" cy="8" rx="3" ry="6.5"/><line x1="1.5" y1="8" x2="14.5" y2="8"/><line x1="2.5" y1="4.5" x2="13.5" y2="4.5"/><line x1="2.5" y1="11.5" x2="13.5" y2="11.5"/></svg>
          <span>www.<span class="accent">veltrowledger</span>.com</span>
        </li>
      </ul>
    </div>
    <div class="address">842 E Alder Ave Brenmoor, IA 43827</div>
  </section>
</body>
</html>
```